Brenwick Structures Construction Company Seeking Modern Website

We are a small construction company wanting to create a web presence. We don't have much in the way of current content but will get photos as they come in. Attached is a picture of our business card.
The pages we would like on the menu are:
Home
Portfolio
Product Specs
Testimonials
Our Process
Contact
Some designs we like are:
http://www.tovasheds-example.com/
http://www.qrnstructures-example.com/
http://dunholtbarns-example.com/
http://pellingframes-example.com/
Not much requirements other than that so feel free to be creative!
Updates
Target Market(s)
Construction
Commercial and Residential Buildings
Industry/Entity Type
Construction Company
Number of Pages Required
5+ page
Look and feel

```html
<!DOCTYPE html>
<html lang="en">
<head>
<meta charset="utf-8">
<title>Brenwick Structures – Construction Company</title>
<link rel="stylesheet" href="https://fonts.googleapis.com/css2?family=Lato:wght@400;700&family=Open+Sans:wght@400;600;700&family=Raleway:wght@400;500&display=swap">
<style>
:root{
  --brand-blue:#1aa3dd;
  --red:#d8261d;
  --ink:#2a2a2a;
  --white:#fff;
  --black:#000;
  --footer-bar:#161616;
}
*{box-sizing:border-box;margin:0;padding:0}
html,body{width:1200px;height:2247px;overflow:hidden}
body{position:relative;background:var(--white);font-family:"Open Sans",Arial,sans-serif;color:var(--ink)}
.abs{position:absolute}

/* header */
.top-rule{left:0;top:0;width:1200px;height:4px;background:var(--brand-blue)}
.logo{left:112px;top:38px;display:flex;align-items:center;gap:10px}
.logo-dot{width:22px;height:22px;border-radius:50%;background:var(--red)}
.logo-name{font-family:"Lato",sans-serif;font-weight:700;font-size:26px;color:#1c5fae;letter-spacing:.3px}
.nav-item{top:50px;font-family:"Lato",sans-serif;font-size:12px;font-weight:400;color:#111;letter-spacing:.1px;white-space:nowrap;text-decoration:none}
.nav-item.active{color:var(--brand-blue)}
.search-btn{left:1053px;top:38px;width:33px;height:33px;border:2px solid var(--brand-blue);border-radius:50%}

/* hero */
.hero{left:0;top:112px;width:1200px;height:398px;background:linear-gradient(160deg,#3e4f60 0%,#6d7f91 35%,#8a7662 60%,#c78a4a 85%,#705842 100%)}
.hero-shade{left:0;top:112px;width:1200px;height:398px;background:rgba(0,0,0,.32)}
.hero-title{left:0;top:232px;width:1200px;text-align:center;font-family:"Lato",sans-serif;font-size:27px;font-weight:400;color:var(--white)}
.hero-text{left:200px;top:284px;width:800px;text-align:center;font-size:14px;line-height:22px;color:var(--white)}
.btn{display:flex;align-items:center;justify-content:center;color:var(--white);font-size:14px;font-family:"Open Sans",sans-serif}
.btn-red{background:var(--red)}
.hero-read{left:482px;top:353px;width:106px;height:47px}
.hero-contact{left:612px;top:353px;width:106px;height:47px;border:2px solid var(--white)}
.hero-dots{left:582px;top:425px;display:flex;gap:7px}
.hero-dots span{width:7px;height:7px;border-radius:50%;background:rgba(255,255,255,.6)}
.hero-dots span:first-child{background:var(--white)}

/* category cards */
.cat{top:465px;width:316px;height:167px;overflow:hidden}
.cat-photo{width:100%;height:100%}
.cat-label{position:absolute;left:0;bottom:0;width:100%;height:31px;background:rgba(30,30,30,.75);color:var(--white);font-family:"Lato",sans-serif;font-size:17px;text-align:center;line-height:31px}

.section-title{left:0;width:1200px;text-align:center;font-family:"Lato",sans-serif;font-size:21px;font-weight:400;color:var(--red)}
.what-text{left:145px;top:727px;width:910px;text-align:center;font-size:11.5px;line-height:22px;color:#444}
.what-btn{left:553px;top:807px;width:95px;height:32px;font-size:13px}

/* portfolio */
.portfolio-band{left:0;top:865px;width:1200px;height:307px;background:linear-gradient(180deg,#e9e9e9,#e2e2e2)}
.band-sub{left:0;width:1200px;text-align:center;font-size:13.5px;color:#555}
.thumb{top:975px;width:160px;height:145px;border:5px solid var(--white);box-shadow:0 1px 4px rgba(0,0,0,.2)}
.arrow{top:1036px;width:14px;height:22px}

/* news */
.news{top:1268px;width:311px;height:175px;overflow:hidden}
.news-photo{width:100%;height:100%}
.news-date{position:absolute;left:0;top:8px;background:var(--red);color:var(--white);font-size:11.5px;font-weight:700;padding:3px 9px}
.news-caption{position:absolute;left:0;bottom:0;width:100%;height:55px;background:linear-gradient(180deg,rgba(0,0,0,0),rgba(0,0,0,.7));color:var(--white);font-size:14.5px;line-height:18px;text-align:center;padding-top:16px}

/* testimonial */
.testimonial-band{left:0;top:1483px;width:1200px;height:442px;background:linear-gradient(180deg,#14b2ec,#109fd9)}
.testimonial-title{color:var(--white);font-size:20px}
.testimonial-sub{color:#d6f1fc}
.collage{left:120px;top:1580px;width:560px;height:320px}
.quote{left:698px;top:1614px;width:352px;font-size:11.5px;font-weight:700;line-height:22px;color:var(--white);text-align:justify}
.quote-btn{left:698px;top:1733px;width:97px;height:31px;font-size:13px}

/* footer */
.footer{left:0;top:1925px;width:1200px;height:277px;background:var(--black)}
.footer-title{font-family:"Raleway",sans-serif;font-size:20px;font-weight:400;color:var(--white)}
.quick-links{left:145px;top:1991px;list-style:none;font-family:"Lato",sans-serif;font-size:12px;color:var(--white)}
.quick-links li{height:26px;line-height:26px}
.field{background:var(--white);border-radius:3px;font-size:12px;font-style:italic;color:#444;padding-left:14px;line-height:32px}
.submit{left:380px;top:2153px;width:106px;height:34px;background:var(--brand-blue);font-size:13px}
.social{left:940px;top:1998px;display:flex;gap:9px}
.social span{width:24px;height:24px;border-radius:2px}
.bottom-bar{left:0;top:2202px;width:1200px;height:45px;background:var(--footer-bar);text-align:center;font-size:10px;color:#aaa;line-height:45px}
</style>
</head>
<body>
<div class="abs top-rule"></div>
<header>
  <div class="abs logo"><span class="logo-dot"></span><span class="logo-name">Brenwick Structures</span></div>
  <nav>
    <a class="abs nav-item active" style="left:449px">HOME</a>
    <a class="abs nav-item" style="left:517px">PORTFOLIO</a>
    <a class="abs nav-item" style="left:614px">PRODUCT SPECS</a>
    <a class="abs nav-item" style="left:739px">TESTIMONIALS</a>
    <a class="abs nav-item" style="left:854px">OUR PROCESS</a>
    <a class="abs nav-item" style="left:965px">CONTACT</a>
  </nav>
  <div class="abs search-btn">
    <svg width="29" height="29" viewBox="0 0 29 29"><circle cx="13.5" cy="13.5" r="4" fill="none" stroke="#1aa3dd" stroke-width="2"/><line x1="16.5" y1="16.5" x2="19.5" y2="19.5" stroke="#1aa3dd" stroke-width="2"/></svg>
  </div>
</header>

<section>
  <div class="abs hero" role="img" aria-label="Construction site with glass towers, scaffolding and white hard hats"></div>
  <div class="abs hero-shade"></div>
  <h1 class="abs hero-title">Lorem ipsum dolor sit amet, sit habemus scaevola senserit ut</h1>
  <p class="abs hero-text">Cum tractatos gubergren at, nominavi probatus pri ex. Vim postea facilis deterruisset in. Eu quo assum mundi. Clita putent reformidans id sea, duo nullam veritus tincidunt ei.</p>
  <div class="abs btn btn-red hero-read">Read More</div>
  <div class="abs btn hero-contact">Contact Us</div>
  <div class="abs hero-dots"><span></span><span></span><span></span></div>
</section>

<section>
  <div class="abs cat" style="left:105px"><div class="cat-photo" role="img" aria-label="Suburban house with green lawn" style="background:linear-gradient(180deg,#8fb9e4 0%,#c9d8e6 40%,#6f6158 60%,#4f8a33 100%)"></div><div class="cat-label">COMMERCIAL</div></div>
  <div class="abs cat" style="left:443px"><div class="cat-photo" role="img" aria-label="Modern residential apartment block against blue sky" style="background:linear-gradient(180deg,#3f7fd0 0%,#7aa6dc 35%,#c9c3bd 65%,#8d6e63 100%)"></div><div class="cat-label">RESIDENTIAL</div></div>
  <div class="abs cat" style="left:781px"><div class="cat-photo" role="img" aria-label="Bright white living room interior" style="background:linear-gradient(180deg,#d9dcdd 0%,#f2f2f0 50%,#c8c6c0 100%)"></div><div class="cat-label">ARCHITECURE</div></div>
</section>

<section>
  <h2 class="abs section-title" style="top:676px">WHAT WE DO?</h2>
  <p class="abs what-text">Erat fringilla aenean pulvinar condimentum velit urna, suspendisse vivam us duis gravida lorem. Ornare sit diam mori lobortis. Ut erat fusce tempor turpis. Erat fringilla aenean pulvinar condimentum velit urna, suspendisse vivam us duis gravida lorem. Ornare sit diam mori lobortis. Ut erat fusce tempor turpis. Erat fringilla aenean pulvinar condimentum velit urna, suspendisse vivam us duis gravida lorem. Ornare sit diam mori lobortis. Ut erat fusce tempor turpis.</p>
  <div class="abs btn btn-red what-btn">Read more</div>
</section>

<section>
  <div class="abs portfolio-band" role="img" aria-label="Faded construction crane and building frame behind"></div>
  <h2 class="abs section-title" style="top:888px">PORTFOLIO</h2>
  <p class="abs band-sub" style="top:920px">Erat fringilla aenean pulvinar condimentum velit urna, suspendisse vivam us duis gravida lorem. Ornare sit diam mori lobortis.</p>
  <svg class="abs arrow" style="left:114px" viewBox="0 0 14 22"><polyline points="10,5 4,11 10,17" fill="none" stroke="#d8261d" stroke-width="2"/></svg>
  <svg class="abs arrow" style="left:1074px" viewBox="0 0 14 22"><polyline points="4,5 10,11 4,17" fill="none" stroke="#d8261d" stroke-width="2"/></svg>
  <div class="abs thumb" style="left:141px;background:linear-gradient(180deg,#6fa3e0 0%,#e4c89a 55%,#4d8a34 100%)" role="img" aria-label="Two-storey family house"></div>
  <div class="abs thumb" style="left:331px;background:linear-gradient(180deg,#8a9a88 0%,#c6c4bd 50%,#8f8a84 100%)" role="img" aria-label="Patio with glass pavilion"></div>
  <div class="abs thumb" style="left:521px;background:linear-gradient(180deg,#3f7fd0 0%,#e6eaee 45%,#9fb2c1 75%,#5b8f3d 100%)" role="img" aria-label="White modern office building"></div>
  <div class="abs thumb" style="left:710px;background:linear-gradient(180deg,#8fbbe6 0%,#d7d0c8 45%,#5a9d35 100%)" role="img" aria-label="House with wide green lawn"></div>
  <div class="abs thumb" style="left:899px;background:linear-gradient(180deg,#6fa3e0 0%,#e4c89a 55%,#4d8a34 100%)" role="img" aria-label="Two-storey family house"></div>
</section>

<section>
  <h2 class="abs section-title" style="top:1214px;font-weight:700;font-size:20px">LATEST NEWS</h2>
  <article class="abs news" style="left:111px"><div class="news-photo" role="img" aria-label="Red house with tiled roof" style="background:linear-gradient(160deg,#7c8a9a 0%,#c5596c 45%,#3f6b2e 100%)"></div><span class="news-date">18-NOV-2015</span><div class="news-caption">Lorem ipsum dolor sit amet, contetur<br>adipiscing elit, sed do eiusmod</div></article>
  <article class="abs news" style="left:446px"><div class="news-photo" role="img" aria-label="Construction workers in hard hats" style="background:linear-gradient(160deg,#e8e2d6 0%,#d8b478 45%,#8a7a6a 100%)"></div><span class="news-date">18-NOV-2015</span><div class="news-caption">Lorem ipsum dolor sit amet, contetur<br>adipiscing elit, sed do eiusmod</div></article>
  <article class="abs news" style="left:781px"><div class="news-photo" role="img" aria-label="Family house with trees" style="background:linear-gradient(180deg,#5e8fd0 0%,#c9c6c2 45%,#4a7d2e 100%)"></div><span class="news-date">18-NOV-2015</span><div class="news-caption">Lorem ipsum dolor sit amet, contetur<br>adipiscing elit, sed do eiusmod</div></article>
</section>

<section>
  <div class="abs testimonial-band" role="img" aria-label="Blue tinted building facade behind"></div>
  <h2 class="abs section-title testimonial-title" style="top:1506px">TESTIMONIAL</h2>
  <p class="abs band-sub testimonial-sub" style="top:1538px">Erat fringilla aenean pulvinar condimentum velit urna, suspendisse vivam us duis gravida lorem. Ornare sit diam mori lobortis.</p>
  <svg class="abs collage" viewBox="0 0 560 320" role="img" aria-label="Diamond grid of client portrait photos">
    <g stroke="#fff" stroke-width="3">
      <polygon points="162,7 238,83 162,159 86,83" fill="#a8a09a"/>
      <polygon points="314,7 390,83 314,159 238,83" fill="#c9b7a2"/>
      <polygon points="467,7 543,83 467,159 391,83" fill="#bdb3a8"/>
      <polygon points="85,83 161,159 85,235 9,159" fill="#b9a89a"/>
      <polygon points="391,83 467,159 391,235 315,159" fill="#8f8780"/>
      <polygon points="162,160 238,236 162,312 86,236" fill="#c4b3a6"/>
      <polygon points="314,160 390,236 314,312 238,236" fill="#b0aaa4"/>
      <polygon points="238,105 292,159 238,213 184,159" fill="#9c9c9c"/>
    </g>
    <rect x="176" y="165" width="96" height="40" fill="#d8261d"/>
    <text x="224" y="181" text-anchor="middle" font-family="Open Sans, sans-serif" font-weight="700" font-size="12" fill="#fff">Mark Halden</text>
    <text x="224" y="198" text-anchor="middle" font-family="Open Sans, sans-serif" font-size="11" fill="#fff">Member</text>
  </svg>
  <p class="abs quote">Erat fringilla aenean pulvinar condimentum velit urna, suspendisse vivam us duis gravida lorem. Ornare sit diam mori lobortis. Ut erat fusce tempor turpis. Erat fringilla aenean pulvinar condimentum velit urna, suspendisse vivam us duis gravida lorem. Ornare sit diam mori lobortis.</p>
  <div class="abs btn btn-red quote-btn">Read more</div>
</section>

<footer>
  <div class="abs footer"></div>
  <h3 class="abs footer-title" style="left:140px;top:1950px">Quick Links</h3>
  <ul class="abs quick-links">
    <li>HOME</li><li>PORTFOLIO</li><li>PRODUCT SPECS</li><li>TESTIMONIALS</li><li>OUR PROCESS</li><li>CONTACT</li>
  </ul>
  <h3 class="abs footer-title" style="left:375px;top:1953px">Quick Enquiry</h3>
  <div class="abs field" style="left:378px;top:2000px;width:204px;height:32px">First Name:</div>
  <div class="abs field" style="left:602px;top:2000px;width:204px;height:32px">Last Name:</div>
  <div class="abs field" style="left:378px;top:2044px;width:204px;height:32px">Email:</div>
  <div class="abs field" style="left:602px;top:2044px;width:204px;height:32px">Phone:</div>
  <div class="abs field" style="left:378px;top:2087px;width:428px;height:47px;line-height:36px">Message:</div>
  <div class="abs btn submit">SUBMIT</div>
  <h3 class="abs footer-title" style="left:940px;top:1953px">Follow Us</h3>
  <div class="abs social">
    <span style="background:#3b5a9a"></span><span style="background:#2fa9d8"></span><span style="background:#2a6fa8"></span><span style="background:#d8d8d8"></span>
  </div>
  <div class="abs bottom-bar">© 2015 • www.brenwickstructures-example.com • PRIVACY POLICY</div>
</footer>
</body>
</html>
```